Bring me business with this creative business card

Design my new business card. I am looking for something different with an impact. People will take a look at this card & they will 1- see how different & creative I am, 2-understand what I do 3- Call me to meet me!

I make videos with a message, testimonials. I am dynamic, fun, creative & human. My new website is in construction but in the meantime you can check this old one: brightpath.ca & another one Tidebloom.com & tidebloom facebook page.
I make videos. sometimes with a cameraman, sometimes with my phone. As an ex Public Relations agent, the message is the most important thing for me. I want to make my clients shine! When they start with me they often remind me of a lamb, when I finish coaching them they are powerful like LIONS! That's why I need a powerful business card!

Target Market(s)

Entrepreneurs, solo entrepreneurs, small & medium companies & start ups. People i will meet while networking. People that need videos on their website & social Networks to get attention, to be visible. men & women. From 35 to 49 years old.
I am an ex Public relations agent. I used to send clients in traditional medias, now with videos they have more chances to be seen on google the new media. I do videos of the president, his team, his loyal clients saying how great the company is & expert videos like series so people can be seen for example every 1 st of every month with a short 2 minute video. Also with my 20 years in marketing & communications I can coach & give tips to anybody who needs it.
Target: anybody who would like my old website brightpath.ca & I also have another website but it will be off line soon: tidebloom.com could give you ideas.

Industry/Entity Type

Communications

Contact Information for Business Card

I am in Montreal,So the business cards have to be the usual size like we have in Montreal: 9 cm x 5 cm
Details:My text: Mathilde Tessier Communication coach/Chief Lion. "Creating Videos as unique as you" off: 514-555-0147 cell: 514-555-0183. tidebloom.com
mathilde@tidebloom.com logo facebook, youtube, instagram

Colors
f37122

Requirements
Must have
• Dynamic, happy. Orange. Be creative in the look but NOT the shape of the card. Easy to read. Big enough to read.
Should not have
• No funny shapes: no round, no square, just the usual. I love creative but NOT on shape.

```html
<!DOCTYPE html>
<html lang="en">
<head>
<meta charset="utf-8">
<title>Tidebloom business card</title>
<link rel="stylesheet" href="https://fonts.googleapis.com/css2?family=Cinzel:wght@600&family=Open+Sans:ital,wght@0,400;0,600;1,400&display=swap">
<style>
  :root {
    --rust: #b4481e;
    --orange: #e15a24;
    --amber: #f0961e;
    --gold: #f7b21a;
    --paper: #f5f4f2;
    --ink: #2a2a2a;
    --light: #f1efec;
    --backdrop: #bdbdbd;
  }
  * { margin: 0; padding: 0; box-sizing: border-box; }
  html, body { width: 1200px; height: 576px; overflow: hidden; }
  body { background: var(--backdrop); position: relative; font-family: "Open Sans", sans-serif; }

  .card { position: absolute; top: 140px; width: 484px; height: 292px; overflow: hidden; }
  .card--front { left: 82px; background: var(--rust); }
  .card--back { left: 602px; background: var(--paper); }

  .brand-dot { position: absolute; border-radius: 50%; }
  .card--front .brand-dot { left: 192px; top: 58px; width: 100px; height: 100px; background: var(--gold); }
  .card--back .brand-dot { left: 78px; top: 70px; width: 88px; height: 88px; background: var(--amber); }

  .brand {
    position: absolute; font-family: "Open Sans", sans-serif; font-weight: 600;
    text-align: center; white-space: nowrap; line-height: 1;
  }
  .card--front .brand { left: 0; width: 100%; top: 186px; font-size: 34px; color: var(--light); }
  .card--back .brand { left: 22px; width: 200px; top: 184px; font-size: 27px; color: var(--orange); }

  .social { position: absolute; left: 22px; width: 200px; top: 236px; text-align: center; font-size: 12px; color: var(--ink); }

  .swoosh { position: absolute; left: 0; top: 0; }

  .site { position: absolute; right: 22px; top: 16px; text-align: right; color: #fff; font-size: 11.5px; line-height: 1.45; }
  .site__slogan { font-style: italic; }

  .person { position: absolute; right: 22px; top: 158px; text-align: right; }
  .person__name { font-family: "Cinzel", serif; font-weight: 600; font-size: 25px; color: var(--orange); letter-spacing: 1px; line-height: 1; }
  .person__role { font-style: italic; font-size: 10.5px; color: var(--ink); margin-top: 5px; }

  .contacts { position: absolute; right: 20px; top: 215px; list-style: none; font-size: 12px; color: var(--ink); }
  .contacts li { display: flex; justify-content: flex-end; align-items: center; gap: 8px; height: 19px; }
  .contacts svg { width: 11px; height: 11px; fill: var(--orange); }
</style>
</head>
<body>
  <section class="card card--front">
    <div class="brand-dot" aria-hidden="true"></div>
    <div class="brand">Tidebloom</div>
  </section>

  <section class="card card--back">
    <svg class="swoosh" width="484" height="292" viewBox="0 0 484 292" aria-hidden="true">
      <path d="M0 0 H130 C80 4 35 14 0 28 Z" fill="var(--orange)"/>
      <path d="M170 0 H484 V124 C420 128 360 108 300 72 C250 40 215 8 170 0 Z" fill="var(--orange)"/>
      <path d="M0 50 C110 2 220 8 290 52 C360 96 420 118 484 116" fill="none" stroke="var(--amber)" stroke-width="7"/>
      <path d="M45 42 C140 18 230 30 290 62 C350 96 420 124 484 128" fill="none" stroke="var(--amber)" stroke-width="3"/>
    </svg>
    <div class="site">
      <div>www.tidebloom.com</div>
      <div class="site__slogan">Creating Videos<br>as unique as you</div>
    </div>
    <div class="brand-dot" aria-hidden="true"></div>
    <div class="brand">Tidebloom</div>
    <div class="social">/tidebloom</div>
    <div class="person">
      <div class="person__name">MATHILDE T.</div>
      <div class="person__role">Communication coach / Chief</div>
    </div>
    <ul class="contacts">
      <li>514-555-0147 <svg viewBox="0 0 24 24"><path d="M6.6 10.8a15 15 0 0 0 6.6 6.6l2.2-2.2c.3-.3.7-.4 1-.2 1.1.4 2.3.6 3.6.6.6 0 1 .4 1 1V20c0 .6-.4 1-1 1A17 17 0 0 1 3 4c0-.6.4-1 1-1h3.5c.6 0 1 .4 1 1 0 1.3.2 2.5.6 3.6.1.3 0 .7-.2 1z"/></svg></li>
      <li>514-555-0183 <svg viewBox="0 0 24 24"><path d="M3 8c0-2 4-4 9-4s9 2 9 4v2h-5V8H8v2H3z M5 12h14l1 8H4z"/></svg></li>
      <li>mathilde@tidebloom.com <svg viewBox="0 0 24 24"><path d="M2 5h20v14H2z M3 6l9 7 9-7" fill="var(--orange)" stroke="#fff" stroke-width="1.5"/></svg></li>
    </ul>
  </section>
</body>
</html>
```